Business Card Design for Flood Rescue 360 - Property Restoration Professionals

I need a business card designed for Flood Rescue 360. We are a full-service property restoration solution. Providing water, fire, smoke & storm restoration as well as mold remediation and full remodel or reconstruction to homes and businesses across Dallas-Fort Worth, TX.
Target Market(s)
home and business owners with insurance covered property damage from water, fire or storm related damage
Industry/Entity Type
property restoration
Contact Information for Business Card
Marcus Pelley General Manager Cell: 214-555-0193 Office: 469-555-0148 email: Marcus@FloodRescue360.example services: Water, Fire, Mold, Reconstruction Tagline: Urgency for Your Water Emergency!
Look and feel
Each slider illustrates characteristics of the customer's brand and the style your logo design should communicate.

```html
<!DOCTYPE html>
<html lang="en">
<head>
<meta charset="utf-8">
<title>Flood Rescue 360 – Business Card</title>
<link href="https://fonts.googleapis.com/css2?family=Montserrat:wght@400;500;700;800&display=swap" rel="stylesheet">
<style>
  :root {
    --brand-blue: #00b0e6;
    --brand-grey: #6f6f6f;
    --ink: #1d1d1d;
    --card: #ffffff;
    --backdrop: #3a3a3a;
  }
  * { box-sizing: border-box; margin: 0; padding: 0; }
  html, body {
    width: 1200px; height: 689px; overflow: hidden;
    background: var(--backdrop);
    font-family: "Montserrat", Arial, sans-serif;
  }
  .stage {
    position: relative; width: 1200px; height: 689px;
    display: flex; align-items: center; justify-content: center; gap: 40px;
  }
  .card {
    position: relative; width: 540px; height: 309px;
    background: var(--card); border-radius: 22px;
    box-shadow: 0 12px 30px rgba(0,0,0,.35);
  }
  /* front */
  .card-front .wordmark {
    position: absolute; left: 44px; top: 58px;
    display: flex; align-items: center; gap: 18px;
  }
  .wordmark-name {
    color: var(--brand-blue); font-weight: 800; text-transform: uppercase;
    font-size: 50px; line-height: .95; letter-spacing: -1px;
  }
  .wordmark-dot {
    width: 96px; height: 96px; border-radius: 50%;
    background: var(--brand-blue); flex: none;
  }
  .services {
    position: absolute; left: 0; right: 0; bottom: 56px;
    display: flex; justify-content: center; align-items: center; gap: 10px;
    font-size: 19px; font-weight: 500; color: var(--ink);
  }
  .services .sep {
    width: 7px; height: 7px; border-radius: 50%; background: var(--brand-blue);
  }
  /* back */
  .card-back .wordmark {
    position: absolute; left: 30px; top: 104px;
    display: flex; align-items: center; gap: 10px;
  }
  .card-back .wordmark-name { font-size: 26px; letter-spacing: -.5px; }
  .card-back .wordmark-dot { width: 48px; height: 48px; }
  .divider {
    position: absolute; left: 258px; top: 42px; width: 2px; height: 170px;
    background: var(--brand-blue);
  }
  .contact { position: absolute; left: 276px; top: 40px; }
  .contact-name {
    color: var(--brand-blue); font-weight: 700; font-size: 25px; line-height: 1.1;
  }
  .contact-title { font-size: 14px; color: var(--ink); margin-bottom: 14px; }
  .contact-list { list-style: none; }
  .contact-list li {
    display: flex; align-items: center; gap: 8px;
    font-size: 12.5px; color: var(--ink); line-height: 1.65;
  }
  .contact-list svg { width: 12px; height: 12px; flex: none; fill: var(--brand-blue); }
  .tagline {
    position: absolute; left: 0; right: 0; bottom: 34px; text-align: center;
    font-size: 16px; color: var(--ink);
  }
</style>
</head>
<body>
<main class="stage">
  <section class="card card-front">
    <div class="wordmark">
      <div class="wordmark-name">Flood<br>Rescue 360</div>
      <div class="wordmark-dot"></div>
    </div>
    <p class="services">
      <span>Water</span><span class="sep"></span>
      <span>Fire</span><span class="sep"></span>
      <span>Mold</span><span class="sep"></span>
      <span>Reconstruction</span>
    </p>
  </section>

  <section class="card card-back">
    <div class="wordmark">
      <div class="wordmark-name">Flood<br>Rescue 360</div>
      <div class="wordmark-dot"></div>
    </div>
    <div class="divider"></div>
    <div class="contact">
      <h1 class="contact-name">Marcus Pelley</h1>
      <p class="contact-title">General Manager</p>
      <ul class="contact-list">
        <li><svg viewBox="0 0 12 12"><path d="M3 0h6a1 1 0 0 1 1 1v10a1 1 0 0 1-1 1H3a1 1 0 0 1-1-1V1a1 1 0 0 1 1-1zm0 1.5v8h6v-8z"/></svg>214-555-0193</li>
        <li><svg viewBox="0 0 12 12"><path d="M1 3c1-2 9-2 10 0l-1 2-2-1V3H4v1L2 5zM2 6h8l1 5H1z"/></svg>469-555-0148</li>
        <li><svg viewBox="0 0 12 12"><path d="M0 2h12v8H0zm1 1v.4l5 3 5-3V3zm0 1.6V9h10V4.6L6 7.6z"/></svg>Marcus@FloodRescue360.example</li>
        <li><svg viewBox="0 0 12 12"><path d="M6 0a6 6 0 1 0 0 12A6 6 0 0 0 6 0zm0 1.2a4.8 4.8 0 0 1 0 9.6 4.8 4.8 0 0 1 0-9.6zM5 3h3L7 6l1 2H5L4 5z"/></svg>FloodRescue360.example</li>
      </ul>
    </div>
    <p class="tagline">Urgency for Your Water Emergency!</p>
  </section>
</main>
</body>
</html>
```